Stationery Design Project

We need a stationery design for our Norwegian trucking company. We have existed for about 15 years and our 12 drivers uses relatively new vehicles to transport goods around in northern Norway. Long distance routes with fresh fish og food transport is our main operations.

We have already made alogo that's printed on our trucks. The logo and a picture of our trucks is attached. I think the logo i crappy, but since its already in use, changing it is not an option in this round. Still using a better colour scheme in the overall stationery and more interesting fonts is possible (altso in the logo).

Company details:
Name: Kjelvraket AS
Organisation nr 873 615 309
Post adress: 8642 Raudvik

I like minimalism and simplicity. I am avalibly for questions in normal GMT working hours either here or on mail: ivar@fjordlast.no

Reason: Hi. Im extending the deadline because I needed some time to find a vector file of our logo. Sorry for the inconvenience

Hi, and thanks for all your interest in the project. Some updates:

-          I have decided to commit to using one of the designs. Some designer will get the payment.

-          I have extended the deadline with 24 hours since I needed some time to find our firms vector logo (a slow Swedish man was holding me up)

-          We will not choose a design before the deadline. No need to rush.

-          We have received a lot of great design and think there is a need to specified the product we want to make:

o   Business Card for all our employers. I just need the design and will duplicate with the correct numbers and name myself. The information on should be: Logo, employer’s name, Phone number, email, website, Postal number and address. Use this as a template: logo, Leif Brattvoll, 47382066, Leif@fjordlast.no,, fjordlast.no, 8642 Raudvik. The order and placement of the information is your creative decision.

o   Stickers to put on the goods we travel. On the sticker the should be the following information: Logo, phone number, Tekst and link: Fraktæ av Kjelvraket. Ke du syns? Fjordlast.no/tilbakemelding (this means: Handled by Kjelvraket. What do you think Fjordlast.no/feedback -à the link will be a feedback form). The placement the information and size is your creative decision with some stings: we have been thinking of using Drukko for printing and see that a size about 6x6 cm, 8x5 or something like that. (with 3000 copies our budget is 200 punds). Any suggestions of other suppliers are welcome. Drukko price calculator http://www.drukkolabelhouse.co.uk/digital-litho-printing/printing-labels-tags/stickers/

o   Letterhead with logo, address, phone number and organizational number.

o   Envelopes with logo,address, phone number and organizational number.

Have a nice day.

 

 

• Using the blue colour in the logo and using a similar graphic approch.

```html
<!DOCTYPE html>
<html lang="no">
<head>
<meta charset="utf-8">
<title>Kjelvraket AS – visittkort</title>
<link rel="stylesheet" href="https://fonts.googleapis.com/css2?family=Open+Sans:wght@400;700&display=swap">
<style>
  :root {
    --stage: #2a2a2c;
    --card-white: #ffffff;
    --card-dark: #1d1b1b;
    --brand-blue: #1656a8;
    --brand-blue-deep: #0c3f86;
    --ink: #3a3a3a;
    --muted: #8a8a8a;
    --stripe-dark: #111111;
    --stripe-grey: #9a9a9a;
  }
  * { box-sizing: border-box; margin: 0; padding: 0; }
  html, body { width: 1200px; height: 250px; overflow: hidden; }
  body {
    background: var(--stage);
    font-family: "Open Sans", Arial, sans-serif;
    position: relative;
  }
  .card {
    position: absolute;
    top: 20px;
    width: 359px;
    height: 208px;
    border-radius: 12px;
    overflow: hidden;
  }
  .card--front { left: 16px; background: var(--card-white); }
  .card--back-light { left: 411px; background: var(--card-white); }
  .card--back-dark { left: 805px; background: var(--card-dark); }

  .wordmark {
    position: absolute;
    display: flex;
    align-items: center;
    gap: 8px;
    font-weight: 700;
    font-size: 26px;
    color: var(--brand-blue);
    letter-spacing: -0.3px;
    line-height: 1;
  }
  .wordmark__dot {
    width: 14px; height: 14px; border-radius: 50%;
    background: var(--brand-blue);
  }
  .card--front .wordmark { left: 40px; top: 48px; }
  .card--back-light .wordmark,
  .card--back-dark .wordmark {
    left: 50%; top: 88px; transform: translateX(-50%);
    font-size: 30px;
  }

  .contact {
    position: absolute;
    left: 276px;
    top: 44px;
    color: var(--ink);
    font-size: 9.5px;
    line-height: 17px;
  }
  .contact__name { font-size: 12px; margin-bottom: 2px; }

  .wave { position: absolute; left: 0; bottom: 0; width: 359px; height: 208px; }

  .postal {
    position: absolute;
    left: 18px;
    top: 168px;
    color: #ffffff;
    font-size: 9px;
    line-height: 13px;
  }

  .site {
    position: absolute;
    left: 0; right: 0;
    top: 180px;
    text-align: center;
    font-size: 8.5px;
    letter-spacing: 3.2px;
    color: var(--ink);
  }
  .card--back-dark .site { color: #c9c9c9; }
</style>
</head>
<body>

  <section class="card card--front" aria-label="Visittkort forside">
    <svg class="wave" viewBox="0 0 359 208" aria-hidden="true">
      <path d="M0,150 C110,150 240,190 359,128" fill="none" stroke="var(--stripe-grey)" stroke-width="3"/>
      <path d="M0,156 C110,156 240,196 359,136 L359,146 C240,202 110,164 0,164 Z" fill="var(--stripe-dark)"/>
      <path d="M0,166 C110,166 240,204 359,150 L359,208 L0,208 Z" fill="var(--brand-blue)"/>
      <path d="M0,180 C120,180 240,208 359,170 L359,208 L0,208 Z" fill="var(--brand-blue-deep)" opacity="0.45"/>
    </svg>

    <div class="wordmark"><span class="wordmark__dot"></span>Kjelvraket</div>

    <div class="contact">
      <p class="contact__name">Leif Brattvoll</p>
      <p>47382066</p>
      <p>Leif@fjordlast.no</p>
      <p>www.fjordlast.no</p>
    </div>

    <div class="postal">
      <p>8642 Raudvik.</p>
      <p>Organisation nr 873 615 309</p>
    </div>
  </section>

  <section class="card card--back-light" aria-label="Visittkort bakside lys">
    <div class="wordmark"><span class="wordmark__dot"></span>Kjelvraket</div>
    <p class="site">www.fjordlast.no</p>
  </section>

  <section class="card card--back-dark" aria-label="Visittkort bakside mørk">
    <div class="wordmark"><span class="wordmark__dot"></span>Kjelvraket</div>
    <p class="site">www.fjordlast.no</p>
  </section>

</body>
</html>
```